Web page for a garment manufacturing company

We are clothing manufacturer based in Romania.
With our recent expansion, we have significantly increased our internal capacity, allowing us to take on new partnerships and deliver high-quality production services.
Our expertise includes producing classic coats, blazers, trousers, skirts, dresses, and blouses, though we are flexible and open to working with various other textile products.

Target Market(s)

High-end market and luxury

Industry/Entity Type

Garments Manufacturer

Coding

Coded - Design and coding required

Number of Pages Required

1 page

Colors

Designer to choose only greyscale colors for use in the design.

Requirements
Must have
• Velmora logo from our presentation
Nice to have
• https://www.lorvani.pt/
Should not have
• prices, wedding dresses, collections

```html
<!DOCTYPE html>
<html lang="en">
<head>
<meta charset="utf-8">
<title>Velmora — Garment Manufacturing</title>
<link rel="stylesheet" href="https://fonts.googleapis.com/css2?family=Lexend:wght@300;400;500&family=Questrial&display=swap">
<style>
:root{
  --ink:#33475b;
  --text:#2b2b2b;
  --muted:#6a6a6a;
  --paper:#ebe7e4;
  --white:#ffffff;
  --sand:#cbb19b;
  --rule:#d6d1cc;
}
*{box-sizing:border-box;margin:0;padding:0}
html,body{width:1200px;height:3231px;overflow:hidden}
body{position:relative;background:var(--white);font-family:"Questrial",sans-serif;color:var(--text)}
.abs{position:absolute}
h1,h2,.heading{font-family:"Lexend",sans-serif;font-weight:500;color:var(--ink)}
.center{left:0;width:1200px;text-align:center}

/* nav */
.nav{top:0;left:0;width:1200px;height:66px;background:var(--paper)}
.brand{font-family:"Lexend",sans-serif;font-weight:300;color:var(--ink)}
.nav .brand{left:110px;top:16px;font-size:29px}
.nav-links{left:509px;top:28px;display:flex;gap:0;font-size:11px;letter-spacing:.3px;color:var(--muted)}
.nav-links span{position:absolute;white-space:nowrap}
.nav-links .active{color:var(--ink)}
.btn{background:var(--ink);color:var(--white);font-family:"Lexend",sans-serif;font-size:14px;display:flex;align-items:center;justify-content:center;letter-spacing:.2px}
.nav .btn{left:1002px;top:19px;width:85px;height:30px;font-size:11px}

/* hero */
.hero{top:66px;left:0;width:1200px;height:411px;background:linear-gradient(180deg,#b8d4ec 0%,#cfdeea 30%,#a9634b 45%,#9a5a45 72%,#b5aba3 82%,#c9c4bf 100%)}
.hero h1{left:110px;top:100px;font-size:29px;line-height:43px;color:#111;font-weight:500}

/* welcome */
.welcome{top:477px;left:0;width:1200px;height:842px;background:var(--paper)}
.section-title{font-size:32px}
.lead{font-size:16px;line-height:34px;color:var(--text)}
.photo{border-radius:0}

/* categories */
.cat{width:129px;height:129px;border-radius:50%}
.cat-label{width:200px;text-align:center;font-size:16px;color:#333;letter-spacing:.3px}
.arrow{width:40px;height:28px;border:1px solid var(--rule);border-radius:14px;background:#fff}

/* benefits */
.benefit{font-size:15px;line-height:34px;letter-spacing:.3px;color:#333;white-space:nowrap}

/* sustainability */
.sustain{top:2134px;left:0;width:1200px;height:729px;background:var(--paper)}
.tile-label{color:#fff;font-family:"Lexend",sans-serif;font-size:14px;line-height:25px;text-align:center;width:100%}

/* footer */
.footer-head{font-family:"Lexend",sans-serif;font-size:17px;color:var(--ink);font-weight:500}
.flink{font-size:13px;color:var(--muted);letter-spacing:.3px;white-space:nowrap}
.vrule{width:1px;height:234px;background:var(--rule)}
</style>
</head>
<body>

<!-- navigation -->
<header class="abs nav">
  <div class="abs brand">Velmora</div>
  <nav class="abs nav-links" style="left:0;top:0">
    <span class="active" style="left:509px;top:29px">HOME</span>
    <span style="left:582px;top:29px">ABOUT US</span>
    <span style="left:681px;top:29px">CATAGORIES</span>
    <span style="left:793px;top:29px">BENEFITS</span>
    <span style="left:886px;top:29px">CONTACT US</span>
  </nav>
  <div class="abs btn">BOOK NOW</div>
</header>

<!-- hero -->
<section class="abs hero" role="img" aria-label="Photo of the brick factory building under a blue sky">
  <h1 class="abs">Crafting Timeless Clothing<br>with Precision.</h1>
</section>

<!-- welcome -->
<section class="abs welcome">
  <h2 class="abs center section-title" style="top:60px">Welcome To Velmora</h2>
  <p class="abs center lead" style="top:120px">Velmora is a manufacturing company for Ready-to-wear, situated in Brasova, a city with a rich<br>tradition in the clothing industry. The top management is international, and we are proud to have a diverse<br>and dynamic group of professionals from different countries working together.</p>
  <div class="abs photo" style="left:112px;top:382px;width:192px;height:192px;background:linear-gradient(160deg,#7a4a2e,#e07a2a 60%,#3b2a22)" role="img" aria-label="Team photo in orange shirts"></div>
  <div class="abs photo" style="left:317px;top:270px;width:335px;height:193px;background:linear-gradient(180deg,#cfd2d4,#8a8f95 55%,#a88a62)" role="img" aria-label="Production hall with garment racks"></div>
  <div class="abs photo" style="left:663px;top:309px;width:156px;height:154px;background:linear-gradient(170deg,#6b5a4a,#d98a35 55%,#3a3330)" role="img" aria-label="Shelves with decorated pumpkins"></div>
  <div class="abs photo" style="left:831px;top:383px;width:257px;height:241px;background:linear-gradient(180deg,#d8d6de,#c9508f 35%,#3f7fa8 65%,#2a2a2e)" role="img" aria-label="Worker at a pressing table"></div>
  <div class="abs photo" style="left:317px;top:476px;width:156px;height:153px;background:linear-gradient(180deg,#e4e6ea,#6f86a8 60%,#cfd2d6)" role="img" aria-label="Tailor cutting fabric"></div>
  <div class="abs photo" style="left:485px;top:476px;width:334px;height:231px;background:linear-gradient(100deg,#bfc2c4,#e8e6e2 40%,#6d86ad 75%,#4a6595)" role="img" aria-label="Worker checking white and blue jackets"></div>
  <div class="abs btn" style="left:489px;top:743px;width:221px;height:40px">LEARN MORE ABOUT US</div>
</section>

<!-- categories -->
<section class="abs" style="top:1319px;left:0;width:1200px;height:815px">
  <h2 class="abs center section-title" style="top:70px">Our Categories</h2>
  <div class="abs arrow" style="left:34px;top:208px"><svg width="40" height="28"><path d="M27 14H13M18 9l-5 5 5 5" fill="none" stroke="#222" stroke-width="1.5"/></svg></div>
  <div class="abs arrow" style="left:1124px;top:208px"><svg width="40" height="28"><path d="M13 14h14M22 9l5 5-5 5" fill="none" stroke="#222" stroke-width="1.5"/></svg></div>

  <div class="abs cat" style="left:112px;top:157px;background:radial-gradient(circle,#5a5550,#3a2e28)" role="img" aria-label="Classic coat on a mannequin"></div>
  <div class="abs cat" style="left:281px;top:157px;background:radial-gradient(circle,#d8283a,#e67a8a)" role="img" aria-label="Red and white blazers"></div>
  <div class="abs cat" style="left:451px;top:157px;background:radial-gradient(circle,#f2f2f2,#c9c9c9)" role="img" aria-label="White shorts trousers"></div>
  <div class="abs cat" style="left:621px;top:157px;background:radial-gradient(circle,#e9ddd0 45%,#000 47%)" role="img" aria-label="Pleated beige skirt"></div>
  <div class="abs cat" style="left:790px;top:157px;background:radial-gradient(circle,#9dc3d6,#4a6a82)" role="img" aria-label="Light blue dresses"></div>
  <div class="abs cat" style="left:959px;top:157px;background:radial-gradient(circle,#6f97d0,#dfe3e8)" role="img" aria-label="Blue blouse on hanger"></div>

  <div class="abs cat-label" style="left:76px;top:311px">CLASSIC COATS</div>
  <div class="abs cat-label" style="left:245px;top:311px">BLAZERS</div>
  <div class="abs cat-label" style="left:415px;top:311px">TROUSERS</div>
  <div class="abs cat-label" style="left:585px;top:311px">SKIRTS</div>
  <div class="abs cat-label" style="left:754px;top:311px">DRESSES</div>
  <div class="abs cat-label" style="left:923px;top:311px">BLOUSES</div>

  <h2 class="abs center section-title" style="top:396px">Extra Benefits For People</h2>
</section>

<!-- benefits diagram -->
<svg class="abs" style="left:0;top:1760px" width="1200" height="374" viewBox="0 1760 1200 374">
  <circle cx="600" cy="2128" r="300" fill="none" stroke="#33475b" stroke-width="1.5" stroke-dasharray="6 5"/>
  <circle cx="600" cy="2128" r="244" fill="#33475b"/>
  <circle cx="600" cy="2128" r="224" fill="#cbb19b"/>
  <g fill="#33475b" stroke="#dfe3e8" stroke-width="4">
    <circle cx="600" cy="1824" r="30"/>
    <circle cx="387" cy="1921" r="30"/>
    <circle cx="823" cy="1921" r="30"/>
    <circle cx="315" cy="2075" r="30"/>
    <circle cx="889" cy="2075" r="30"/>
  </g>
  <g fill="none" stroke="#fff" stroke-width="1.6" stroke-linejoin="round">
    <rect x="588" y="1813" width="24" height="18" rx="2" transform="rotate(-30 600 1822)"/>
    <path d="M594 1822h10" transform="rotate(-30 600 1822)"/>
    <path d="M374 1928l8-8 6 4 6-4 8 8M372 1922l6-6 6 4M402 1922l-6-6-6 4"/>
    <circle cx="382" cy="1908" r="3"/><circle cx="392" cy="1908" r="3"/>
    <rect x="810" y="1914" width="24" height="15" rx="2"/><path d="M810 1919h24M814 1925h6"/>
    <path d="M302 2082h26v-6l-4-6h-18l-4 6z"/><circle cx="308" cy="2083" r="3"/><circle cx="322" cy="2083" r="3"/>
    <circle cx="315" cy="2062" r="5"/>
    <rect x="878" y="2063" width="18" height="22" rx="2"/><path d="M887 2068v8M883 2072h8"/>
    <path d="M893 2078l6-2 6 2v5c0 3-3 5-6 6-3-1-6-3-6-6z"/>
  </g>
  <text x="600" y="2048" text-anchor="middle" font-family="Lexend, sans-serif" font-weight="300" font-size="58" fill="#33475b">Velmora</text>
</svg>
<div class="abs benefit" style="left:658px;top:1786px">FOOD TICKETS</div>
<div class="abs benefit" style="left:0;width:326px;text-align:right;top:1870px">LAWYER FOR EMPLOYEE'S,<br>LEGAL SERVICES</div>
<div class="abs benefit" style="left:874px;top:1870px">LOYALTY CARDS WITH<br>DISCOUNTS ON DIFFERENT<br>LOCALLY FACILITIES</div>
<div class="abs benefit" style="left:0;width:263px;text-align:right;top:2025px">PAID TRANSPORTATION<br>FOR EMPLOYEES, IN<br>VERY GOOD CONDITIONS</div>
<div class="abs benefit" style="left:940px;top:2025px">HEALTH INSURANCE &amp;<br>MEDICAL SERVICES,<br>REIMBURSED</div>

<!-- sustainability -->
<section class="abs sustain">
  <h2 class="abs center section-title" style="top:58px">Sustainabilty Strategy</h2>
  <p class="abs center lead" style="top:119px">Our commitment to sustainability ensures that every material we use meets strict environmental standards,<br>so you can feel good about the clothes you wear. We can offer a complete flow of services, from sourcing<br>fabrics and trims to samples development, pattern construction, sizing and duplication.</p>
  <div class="abs" style="left:112px;top:349px;width:167px;height:257px;background:linear-gradient(180deg,#c9d6df,#2f6a35 45%,#1e3d24)" role="img" aria-label="Green target in a hand">
    <div class="abs tile-label" style="top:188px">ENVIRONMENT<br>STRATEGY</div>
  </div>
  <div class="abs" style="left:296px;top:260px;width:608px;height:346px;background:linear-gradient(100deg,#d9c8b0,#a7b9cf 40%,#5a6d8a 70%,#3d4a3e)" role="img" aria-label="Three women folding clothes in a studio">
    <div class="abs tile-label" style="top:295px">ZERO WASTE PROJECT</div>
  </div>
  <div class="abs" style="left:920px;top:260px;width:167px;height:257px;background:linear-gradient(180deg,#a8793f,#d8b887 35%,#3e5a2c 70%,#26311f)" role="img" aria-label="Green globe held in front of a suit">
    <div class="abs tile-label" style="top:197px">RESPONSIBLE<br>SOURCE</div>
  </div>
  <div class="abs btn" style="left:534px;top:640px;width:131px;height:40px">LEARN MORE</div>
</section>

<!-- footer -->
<footer class="abs" style="top:2863px;left:0;width:1200px;height:368px">
  <div class="abs brand" style="left:115px;top:50px;font-size:50px">Velmora</div>
  <svg class="abs" style="left:122px;top:138px" width="130" height="30">
    <g fill="none" stroke="#33475b" stroke-width="1.4">
      <circle cx="16" cy="15" r="13"/><circle cx="47" cy="15" r="13"/><circle cx="79" cy="15" r="13"/><circle cx="110" cy="15" r="13"/>
    </g>
  </svg>
  <div class="abs vrule" style="left:335px;top:44px"></div>
  <div class="abs vrule" style="left:559px;top:44px"></div>
  <div class="abs vrule" style="left:789px;top:44px"></div>

  <div class="abs footer-head" style="left:395px;top:62px">QUICK LINKS</div>
  <div class="abs flink" style="left:395px;top:107px">HOME</div>
  <div class="abs flink" style="left:395px;top:138px">ABOUT US</div>
  <div class="abs flink" style="left:395px;top:169px">CATAGORIES</div>
  <div class="abs flink" style="left:395px;top:200px">BENEFITS</div>
  <div class="abs flink" style="left:395px;top:231px">CONTACT US</div>

  <div class="abs footer-head" style="left:609px;top:62px">OTHER LINKS</div>
  <div class="abs flink" style="left:609px;top:107px">PRIVACY POLICY</div>
  <div class="abs flink" style="left:609px;top:138px">TERMS OF USE</div>
  <div class="abs flink" style="left:609px;top:169px">SITE MAP</div>
  <div class="abs flink" style="left:609px;top:200px">CLOTHING</div>

  <div class="abs footer-head" style="left:841px;top:62px">CONTACT US</div>
  <svg class="abs" style="left:841px;top:108px" width="34" height="150">
    <g fill="none" stroke="#33475b" stroke-width="1.4">
      <circle cx="17" cy="17" r="15"/><circle cx="17" cy="67" r="15"/><circle cx="17" cy="119" r="15"/>
      <path d="M12 10c-2 2-1 6 3 10s8 5 10 3l-2-3-3 1-5-5 1-3z" fill="#33475b" stroke="none"/>
      <rect x="10" y="62" width="14" height="10" fill="#33475b" stroke="none"/>
      <path d="M10 62l7 6 7-6" stroke="#fff" stroke-width="1"/>
      <path d="M17 128c-4-5-6-8-6-11a6 6 0 0 1 12 0c0 3-2 6-6 11z"/><circle cx="17" cy="117" r="2"/>
    </g>
  </svg>
  <div class="abs flink" style="left:889px;top:118px">40 300 555 018</div>
  <div class="abs flink" style="left:889px;top:168px">INFO@VELMORAFASHION.COM</div>
  <div class="abs flink" style="left:889px;top:219px;line-height:31px">BRASOVA STR. TEILOR 7,<br>ZIP CODE: 610450</div>

  <div class="abs" style="left:110px;top:301px;width:978px;height:1px;background:var(--rule)"></div>
  <div class="abs center flink" style="top:325px">@2024 COPYRIGHTS - <span style="color:var(--ink);font-weight:bold">VELMORA</span> - ALL RIGHTS RESERVED</div>
</footer>

</body>
</html>
```